Shopping centre customer engagement software website

We need a multi page site with :

*What we do.
*How it works.
*Benefits
* Case study
* Testimonial
* Business login (we provide link to business portal)
* Consumer login (we provide link to consumer site)
* Book a demo
* Contact us

We want it to be clean and crisp and very self explanatory with little clutter. We are thinking white but are open to what ever looks the best.
Updates

Wordpress is preferred

Need extra days to review

Target Market(s)

Shopping centre managers and retail property companies

Coding

Coded - Design and coding required

Number of Pages Required

5+ page

Font styles to use
Sans Serif

Colors
ffffff

Requirements
Must have
• As listed above and must be responsive! Checkout our existing site for the text to be included (will be edited but it’ll give you an idea) www.vostrelink.com

```html
<!DOCTYPE html>
<html lang="en">
<head>
<meta charset="utf-8">
<title>Vostrelink – Shopping centre customer engagement</title>
<link href="https://fonts.googleapis.com/css2?family=Open+Sans:wght@300;400;600;700&display=swap" rel="stylesheet">
<style>
:root{
  --teal:#4fbfd8;
  --teal-dark:#3aaecb;
  --ink:#2b2b2b;
  --body:#6b6b6b;
  --muted:#9a9a9a;
  --rule:#e3e3e3;
  --panel:#f4f4f4;
  --panel-2:#ececec;
  --footer:#3d3d3d;
  --white:#ffffff;
}
*{box-sizing:border-box;margin:0;padding:0}
html,body{width:1200px;height:3614px;overflow:hidden}
body{font-family:"Open Sans",Arial,sans-serif;color:var(--body);background:var(--white);position:relative}
.wrap{width:936px;margin:0 auto;position:relative}
section,header,footer{position:absolute;left:0;width:1200px}

/* header */
.site-header{top:0;height:145px;background:var(--white)}
.brand{position:absolute;left:132px;top:24px;display:flex;align-items:center;gap:14px}
.brand-mark{width:58px;height:58px;border-radius:50%;background:#9aa3ab}
.brand-name{font-size:30px;font-weight:400;letter-spacing:3px;color:#555}
.top-contact{position:absolute;right:132px;top:38px;display:flex;gap:34px;font-size:18px;color:var(--ink)}
.top-contact span{display:flex;align-items:center;gap:10px}
.main-nav{position:absolute;right:132px;top:100px;display:flex;gap:34px;font-size:14px;color:var(--ink)}
.main-nav .active{color:var(--teal)}

/* hero */
.hero{top:145px;height:470px;background:linear-gradient(180deg,#d9dde0 0%,#eef0f1 45%,#cfd3d5 100%)}
.hero-title{position:absolute;top:46px;width:100%;text-align:center}
.hero-title p{font-size:26px;color:var(--ink);margin-bottom:4px}
.hero-title h1{font-size:33px;font-weight:600;color:var(--teal);line-height:1.15;text-transform:uppercase}
.dots{position:absolute;bottom:24px;left:0;width:100%;display:flex;justify-content:center;gap:8px}
.dots i{width:12px;height:12px;border-radius:50%;background:#fff;opacity:.7;display:block}
.dots i:first-child{opacity:1;background:#ddd}

/* shared */
.section-title{text-align:center;color:var(--teal);font-size:33px;font-weight:600;text-transform:uppercase}
.what{top:615px;height:392px}
.what .section-title{margin-top:70px}
.what p{font-size:13.5px;line-height:1.75;text-align:center;margin-top:16px}
.btn-outline{display:block;width:108px;margin:26px auto 0;border:1px solid #ccc;padding:10px 0;text-align:center;font-size:13px;color:var(--muted)}

.how{top:1007px;height:433px;background:var(--panel)}
.how .section-title{margin-top:76px}
.steps{position:absolute;left:132px;top:140px;width:936px;height:240px}
.steps-line{position:absolute;left:80px;right:80px;top:19px;height:2px;background:var(--teal)}
.step{position:absolute;top:0;width:160px;text-align:center}
.step-num{width:38px;height:38px;border-radius:50%;background:var(--teal);color:#fff;font-size:15px;line-height:38px;margin:0 auto;position:relative;z-index:2}
.step-circle{width:160px;height:160px;border-radius:50%;border:2px solid var(--teal);background:var(--white);margin-top:-12px;display:flex;align-items:center;justify-content:center}
.step-label{font-size:14px;font-weight:600;color:var(--ink);margin-top:14px;text-transform:uppercase}

.statement{top:1440px;height:240px;background:linear-gradient(90deg,#f3d9df 0%,#f7efe7 35%,#eef0f2 65%,#f2e2d8 100%)}
.statement p{position:absolute;top:92px;left:150px;width:900px;text-align:center;font-size:17px;font-weight:700;color:#111;line-height:1.5;text-transform:uppercase}

.benefits{top:1680px;height:603px}
.benefits .section-title{margin-top:70px}
.benefit-list{position:absolute;left:132px;top:138px;width:936px}
.benefit{position:absolute;width:430px;display:flex;gap:14px;font-size:13px;line-height:1.8}
.benefit svg{flex:none;margin-top:2px}

.case{top:2283px;height:527px;background:linear-gradient(180deg,#e9e4df 0%,#f3efea 50%,#e6e1dc 100%)}
.case .section-title{margin-top:80px}
.case-sub{text-align:center;font-size:15px;font-weight:600;color:var(--ink);margin-top:4px}
.stats{position:absolute;left:132px;top:166px;width:936px;display:grid;grid-template-columns:repeat(3,297px);column-gap:22px;row-gap:26px}
.stat{background:rgba(255,255,255,.92);height:127px;text-align:center;padding-top:22px}
.stat b{display:block;font-size:46px;font-weight:400;color:var(--teal);line-height:1.1}
.stat span{font-size:15px;color:var(--body)}

.testimonial{top:2810px;height:275px}
.testimonial h2{text-align:center;color:var(--teal);font-size:33px;font-weight:600;text-transform:uppercase;margin-top:70px}
.testimonial blockquote{width:936px;margin:8px auto 0;text-align:center;font-size:16px;line-height:1.7;color:#555}

.contact{top:3085px;height:433px;background:var(--panel)}
.contact-side{position:absolute;left:600px;top:0;width:600px;height:433px;background:var(--panel-2)}
.contact h3{font-size:30px;font-weight:600;color:var(--teal);text-transform:uppercase}
.contact-form{position:absolute;left:132px;top:66px;width:420px}
.contact-form h3{margin-bottom:26px}
.field{border:1px solid #d5d5d5;background:#fff;height:40px;font-size:11px;color:var(--muted);padding:12px 14px}
.row{display:flex;gap:12px;margin-bottom:12px}
.row .field{width:200px}
.btn-send{display:inline-block;background:var(--teal);color:#fff;font-size:13px;padding:11px 16px;margin-top:18px}
.contact-info{position:absolute;left:658px;top:66px;width:420px;font-size:14px;line-height:1.75;color:#777}
.contact-info h3{margin-bottom:16px}
.contact-info p{margin-bottom:18px}

.site-footer{top:3518px;height:96px;background:var(--footer);color:#cfcfcf}
.footer-nav{position:absolute;left:132px;top:25px;display:flex;gap:16px;font-size:11px}
.copyright{position:absolute;left:132px;top:52px;font-size:11px}
.social{position:absolute;right:150px;top:29px;display:flex;gap:16px}
.social i{width:32px;height:32px;border-radius:50%;background:#777;display:block}
</style>
</head>
<body>

<header class="site-header">
  <div class="brand"><span class="brand-mark"></span><span class="brand-name">VOSTRELINK</span></div>
  <div class="top-contact">
    <span><svg width="16" height="12" viewBox="0 0 16 12"><rect width="16" height="12" fill="#222"/><path d="M0 0l8 6 8-6" stroke="#fff" stroke-width="1.4" fill="none"/></svg>contact@vostrelink.com</span>
    <span><svg width="14" height="14" viewBox="0 0 14 14"><path d="M3 1l3 3-1.5 1.5a8 8 0 0 0 4 4L10 8l3 3-2 2C6 13 1 8 1 3z" fill="#222"/></svg>0230419872</span>
  </div>
  <nav class="main-nav">
    <span class="active">What we do</span><span>Benefits</span><span>Testimonials</span><span>How it works</span><span>Case study</span><span>Contact</span>
  </nav>
</header>

<section class="hero" role="img" aria-label="Bright shopping centre mall interior with shop fronts and shoppers">
  <div class="hero-title">
    <p>Vostrelink exceeds all expectations for</p>
    <h1>Shopping centre managers, shoppers,<br>tenants and landlords</h1>
  </div>
  <div class="dots"><i></i><i></i><i></i><i></i></div>
</section>

<section class="what">
  <div class="wrap">
    <h2 class="section-title">What we can do for you</h2>
    <p>Vostrelink provides shopping centre managers with an easy to use platform which enables them to delight their shoppers, impress their tenants, provide detailed data to their landlords and all accessible to them at the click of button.</p>
    <p>Vostrelink gives shopping centres real time tracking through smart ID's of individual customer journeys through their physical stores, enabling highly targeted, relevant and timely promotional and rewarding capabilities. Furthermore, through deep analytical data processing of the customer journey, centre managers will be able to more accurately and reliably predict shopping behaviours.</p>
    <span class="btn-outline">Read more</span>
  </div>
</section>

<section class="how">
  <h2 class="section-title">How it works</h2>
  <div class="steps">
    <div class="steps-line"></div>
    <div class="step" style="left:0">
      <div class="step-num">1</div>
      <div class="step-circle"><svg width="70" height="70" viewBox="0 0 70 70" fill="none" stroke="#333" stroke-width="2"><rect x="10" y="20" width="46" height="30" rx="3" transform="rotate(-30 33 35)"/><line x1="14" y1="40" x2="52" y2="18"/></svg></div>
      <div class="step-label">Allocate cards</div>
    </div>
    <div class="step" style="left:194px">
      <div class="step-num">2</div>
      <div class="step-circle"><svg width="70" height="70" viewBox="0 0 70 70" fill="none" stroke="#333" stroke-width="2"><rect x="24" y="14" width="26" height="44" rx="3"/><line x1="24" y1="50" x2="50" y2="50"/><rect x="12" y="20" width="20" height="12" rx="2"/></svg></div>
      <div class="step-label">Direct marketing</div>
    </div>
    <div class="step" style="left:388px">
      <div class="step-num">3</div>
      <div class="step-circle"><svg width="70" height="70" viewBox="0 0 70 70" fill="none" stroke="#333" stroke-width="2"><path d="M24 40V24h5l6-10c3 0 4 2 3 6l-1 4h9c2 0 3 2 2 4l-3 10c0 2-2 2-3 2H24z"/><path d="M14 54l2 4 4 .5-3 3 1 4-4-2-4 2 1-4-3-3 4-.5z"/><path d="M35 54l2 4 4 .5-3 3 1 4-4-2-4 2 1-4-3-3 4-.5z"/><path d="M56 54l2 4 4 .5-3 3 1 4-4-2-4 2 1-4-3-3 4-.5z"/></svg></div>
      <div class="step-label">Rewarding loyalty</div>
    </div>
    <div class="step" style="left:582px">
      <div class="step-num">4</div>
      <div class="step-circle"><svg width="70" height="70" viewBox="0 0 70 70" fill="none" stroke="#333" stroke-width="2"><path d="M18 16h24l8 8v32H18z"/><path d="M42 16v8h8"/><line x1="24" y1="32" x2="44" y2="32"/><line x1="24" y1="40" x2="44" y2="40"/><line x1="24" y1="48" x2="38" y2="48"/></svg></div>
      <div class="step-label">Collect data</div>
    </div>
    <div class="step" style="left:776px">
      <div class="step-num">5</div>
      <div class="step-circle"><svg width="70" height="70" viewBox="0 0 70 70" fill="none" stroke="#333" stroke-width="2"><line x1="12" y1="56" x2="58" y2="56"/><rect x="16" y="44" width="6" height="12"/><rect x="28" y="38" width="6" height="18"/><rect x="40" y="32" width="6" height="24"/><polyline points="16,36 30,28 40,30 56,14"/><polyline points="50,14 56,14 56,20"/></svg></div>
      <div class="step-label">Data analytics</div>
    </div>
  </div>
</section>

<section class="statement" role="img" aria-label="Soft blurred shop interior with warm pastel lights">
  <p>Understanding your customers and identifying trends are key to a successful shopping centre, with our innovative and effective services Vostrelink can help you lead the way.</p>
</section>

<section class="benefits">
  <h2 class="section-title">The benefits provided by Vostrelink</h2>
  <div class="benefit-list">
    <div class="benefit" style="left:0;top:0"><svg width="18" height="18" viewBox="0 0 18 18"><circle cx="9" cy="9" r="9" fill="#444"/><path d="M5 9l3 3 5-6" stroke="#fff" stroke-width="2" fill="none"/></svg><span>Increase dwell times by setting triggers which send text messages rewarding loyalty E.g. If a shopper has been in the centre for an hour or more, an automatic text will be sent giving the shopper an reward such as free park or a free coffee.</span></div>
    <div class="benefit" style="left:506px;top:0"><svg width="18" height="18" viewBox="0 0 18 18"><circle cx="9" cy="9" r="9" fill="#444"/><path d="M5 9l3 3 5-6" stroke="#fff" stroke-width="2" fill="none"/></svg><span>Provide undisputable proof to your tenants of marketing R.O.I E.g. You can provide metrics that prove out of the 1,000 targeted messages sent to their customers, within the past week, 350 stopped and entered their store. You can show them who their best customers were, how long they stayed in their stores and where they came from etc etc.</span></div>
    <div class="benefit" style="left:0;top:172px"><svg width="18" height="18" viewBox="0 0 18 18"><circle cx="9" cy="9" r="9" fill="#444"/><path d="M5 9l3 3 5-6" stroke="#fff" stroke-width="2" fill="none"/></svg><span>Lower marketing costs by only directly marketing (text message) to your tenants ideal customer segment while they are shopping near their store.</span></div>
    <div class="benefit" style="left:506px;top:172px"><svg width="18" height="18" viewBox="0 0 18 18"><circle cx="9" cy="9" r="9" fill="#444"/><path d="M5 9l3 3 5-6" stroke="#fff" stroke-width="2" fill="none"/></svg><span>Increase and measure customer loyalty through tailored targeted rewards and analytics.</span></div>
    <div class="benefit" style="left:0;top:278px"><svg width="18" height="18" viewBox="0 0 18 18"><circle cx="9" cy="9" r="9" fill="#444"/><path d="M5 9l3 3 5-6" stroke="#fff" stroke-width="2" fill="none"/></svg><span>Easy to install, no wiring required.</span></div>
    <div class="benefit" style="left:506px;top:278px"><svg width="18" height="18" viewBox="0 0 18 18"><circle cx="9" cy="9" r="9" fill="#444"/><path d="M5 9l3 3 5-6" stroke="#fff" stroke-width="2" fill="none"/></svg><span>Easy to use dashboard with one click reporting.</span></div>
    <div class="benefit" style="left:0;top:338px"><svg width="18" height="18" viewBox="0 0 18 18"><circle cx="9" cy="9" r="9" fill="#444"/><path d="M5 9l3 3 5-6" stroke="#fff" stroke-width="2" fill="none"/></svg><span>Know who your customers are personally and when they visit you.</span></div>
    <div class="benefit" style="left:506px;top:338px"><svg width="18" height="18" viewBox="0 0 18 18"><circle cx="9" cy="9" r="9" fill="#444"/><path d="M5 9l3 3 5-6" stroke="#fff" stroke-width="2" fill="none"/></svg><span>Have the data to back up any decision's you make.</span></div>
  </div>
</section>

<section class="case" role="img" aria-label="Blurred clothing boutique interior in soft neutral tones">
  <h2 class="section-title">Case study</h2>
  <p class="case-sub">Results from a 31 day campaign</p>
  <div class="stats">
    <div class="stat"><b>650</b><span>VIP Card Holders</span></div>
    <div class="stat"><b>10,500</b><span>Messages Sent</span></div>
    <div class="stat"><b>22%</b><span>Conversion Rate</span></div>
    <div class="stat"><b>1.2 H</b><span>AVG Dwell Time</span></div>
    <div class="stat"><b>95%</b><span>Tenant Engagement</span></div>
    <div class="stat"><b>980</b><span>Loyalty Rewards Issued</span></div>
  </div>
</section>

<section class="testimonial">
  <h2>Conor Haslett - Millbrook Centre Manager</h2>
  <blockquote>“All of the data captured has now been analysed, equipping us with invaluable insights into shopping and spending patterns, and the impact of our media campaigns – all of which is gold dust as we plan ahead for future focussed campaigns. The flexibility of the Vostrelink operating platform software means we will most certainly use this system again going forward.”</blockquote>
</section>

<section class="contact">
  <div class="contact-side"></div>
  <div class="contact-form">
    <h3>Contact us</h3>
    <div class="row"><div class="field">Name</div><div class="field">Email</div></div>
    <div class="field" style="width:412px">Message</div>
    <span class="btn-send">SEND</span>
  </div>
  <div class="contact-info">
    <h3>Contact info</h3>
    <p>Unit 7b, Harbour Road, Larkfield, BT41 2QX<br>liam@vostrelink.com</p>
    <p>Foundry, 3rd Floor, 48 Canal Side Street, London, SE1 4LT<br>nora@vostrelink.com</p>
    <p>2nd Floor, Weaver House, Linen Row, Belfast<br>owen@vostrelink.com</p>
    <p>Phone | 0230419872<br>Email | contact@vostrelink.com</p>
  </div>
</section>

<footer class="site-footer">
  <nav class="footer-nav"><span>What we do</span><span>|</span><span>Benefits</span><span>|</span><span>Testimonials</span><span>|</span><span>How it works</span><span>|</span><span>Case study</span><span>|</span><span>Contact</span></nav>
  <p class="copyright">Copyright © 2018 Vostrelink. All rights reserved.</p>
  <div class="social"><i></i><i></i><i></i></div>
</footer>

</body>
</html>
```